AMAZING WEBSITE DESIGN NEEDED FOR MAID / CLEANING SERVICE

NOTE: This is Website Design Only - No coding required

Please submit your designs ASAP as we want to pick a winner and get started!

Hey,

We are looking for a new amazing website design for a maid or cleaning service.

They have a horrible website that we want turned into a masterpiece.

As you will see on their current site:

http://brightnookservices.example-host.net/

They have a lot of stuff, very disorganized, and need help.

Here is what we need:

Colors: Same as current site, Orange, Gray, Black

Menu: Horizontal with same Menu items

Need a spot for a video on the homepage

Want content to be structured in a great format that is easy to read.

Want to highlight commercial and residential on the website homepage.

Also want a spot for customer testimonials

We want the site clean, professional, fresh and modern.

Please help by matching the logo design.

I look forward to your designs!
Updates

Hi All! Really appreciate your efforts and designs. I will be meeting with our client on Monday and will then be able to provide feedback after our meeting. If you have other ideas, please submit them. The more I can show him the better! Thanks!

Target Market(s)

The target market is residential home owners as well as commercial businesses who need cleaning on a regular basis.

This company cleans homes and offices for individuals.

Industry/Entity Type

Residential

Font styles to use
Sans Serif

Requirements
Must have
• Must match logo colors
Must have spot for video
Must have a clean look
Must have a bold look
Nice to have
• Highly visual
Should not have
• clutter
messy design
hard to read

```html
<!DOCTYPE html>
<html lang="en">
<head>
<meta charset="utf-8">
<title>Bright Nook – Cleaning Services</title>
<link href="https://fonts.googleapis.com/css2?family=Open+Sans:wght@400;600;700&family=Raleway:wght@300;400;700&display=swap" rel="stylesheet">
<style>
:root{
  --orange:#f0802a;
  --orange-soft:#f39a4a;
  --ink:#222;
  --text:#555;
  --muted:#8a8a8a;
  --line:#e2e2e2;
  --band:#dedede;
  --footer:#4a4a4a;
  --footer-low:#3b3b3b;
  --footer-text:#d6d6d6;
  --white:#fff;
}
*{margin:0;padding:0;box-sizing:border-box}
html,body{width:690px;height:1200px;overflow:hidden;background:var(--white)}
body{position:relative;font-family:"Open Sans",Arial,sans-serif;color:var(--text)}
.abs{position:absolute}

/* header */
.site-header{left:0;top:0;width:690px;height:58px;background:#f7f7f7;border-bottom:1px solid var(--line)}
.brand{left:58px;top:20px;display:flex;align-items:center;gap:5px;font-family:"Open Sans",sans-serif;font-weight:700;font-size:14px;color:var(--orange)}
.brand-mark{width:9px;height:9px;background:var(--orange)}
.phone{right:57px;top:14px;font-size:9.5px;color:#333;display:flex;align-items:center;gap:5px}
.main-nav{top:34px;left:0;width:690px;height:16px;font-size:8.5px;color:#888}
.main-nav span{position:absolute;top:0}
.main-nav .active{color:var(--orange);border-bottom:1px solid var(--orange);padding-bottom:5px}

/* hero */
.hero{left:0;top:58px;width:690px;height:234px;background:linear-gradient(100deg,#6b4a30 0%,#b88c63 22%,#e9e2d8 45%,#f4f1ec 70%,#dcd6cc 100%)}
.hero-panel{left:58px;top:102px;width:217px;height:117px;background:rgba(20,20,20,.78);padding:6px 9px}
.hero-panel h1{font-family:"Raleway",sans-serif;font-weight:300;font-size:17px;color:var(--orange);line-height:21px}
.hero-panel h1 b{font-weight:700;display:block;letter-spacing:.5px}
.hero-panel p{font-size:6.9px;line-height:13.8px;color:#eee;margin-top:5px}

/* welcome */
.welcome{left:0;top:308px;width:690px;text-align:center}
.welcome h2{font-family:"Raleway",sans-serif;font-weight:400;font-size:12.5px;color:#333}
.welcome h2 b{font-weight:700;font-size:15px}
.welcome p{width:420px;margin:7px auto 0;font-size:7px;line-height:12px;color:#666}

/* services */
.service{top:396px;width:190px;display:flex;gap:6px}
.service .thumb{width:58px;height:41px;flex:none;background:linear-gradient(135deg,#d9d4cc,#a89a88);border:1px solid #ddd}
.service h3{font-family:"Raleway",sans-serif;font-weight:400;font-size:11px;color:var(--orange)}
.service p{font-size:6.8px;line-height:9px;color:var(--muted);margin-top:3px}

/* video band */
.section-bar{left:58px;top:462px;width:575px;height:20px;background:var(--band);padding:0 8px;display:flex;align-items:center;justify-content:space-between}
.section-bar h3{font-family:"Raleway",sans-serif;font-weight:400;font-size:11px;color:var(--orange)}
.video{left:58px;top:510px;width:363px;height:189px;border-radius:4px;overflow:hidden;background:linear-gradient(120deg,#2a2a2a,#4a4a48 50%,#2d2d2b)}
.player-bar{position:absolute;left:0;bottom:0;width:100%;height:33px;background:#111}
.player-time{position:absolute;left:47px;top:13px;font-size:6px;color:#fff}
.player-time span{color:#888}
.video-copy{left:430px;top:508px;width:204px}
.video-copy p{font-size:6.8px;line-height:11.5px;color:#222;font-weight:600}
.video-copy ul{list-style:none;margin-top:11px}
.video-copy li{font-size:6.5px;color:#555;line-height:20px;padding-left:12px;position:relative}
.video-copy li::before{content:"";position:absolute;left:1px;top:8px;width:4px;height:4px;border-radius:50%;background:#666}
.watch-btn{left:432px;top:675px;width:107px;height:24px;background:var(--orange-soft);border-bottom:2px solid #d66f1f;border-radius:2px;color:#fff;font-size:10.5px;font-weight:600;text-align:center;line-height:22px}

/* sector cards */
.sector{top:740px;width:180px;text-align:center}
.sector .photo{height:84px}
.sector h4{font-size:10px;font-weight:700;color:#111;margin-top:8px;letter-spacing:.2px}
.sector p{font-size:7.8px;line-height:10px;color:#333;margin-top:4px}

/* testimonial */
.avatar{left:59px;top:896px;width:86px;height:86px;border-radius:50%;background:linear-gradient(180deg,#c9c9c9,#6b6f78);border:2px solid #eee}
.client-name{left:58px;top:996px;width:108px;font-size:6px;font-weight:700;color:#555;text-align:center;letter-spacing:.2px}
.dots{left:86px;top:1013px;display:flex;gap:6px}
.dots i{width:6px;height:6px;border-radius:50%;background:#444;display:block}
.dots i.on{background:none;border:1px solid var(--orange)}
.testimonial-title{left:160px;top:900px;width:376px;text-align:center;font-family:"Raleway",sans-serif;font-size:18.5px;color:#333}
.testimonial-title span{color:var(--orange)}
.quote{font-family:Georgia,serif;font-size:34px;color:#c8c8c8;line-height:1}
.testimonial-text{left:190px;top:947px;width:432px;font-size:6.6px;line-height:11.5px;color:#666}

/* footer */
.site-footer{left:0;top:1058px;width:690px;height:120px;background:var(--footer)}
.footer-col{top:1077px;font-size:7.2px;line-height:13px;color:var(--footer-text)}
.footer-col h5{font-size:9px;font-weight:700;color:#fff;margin-bottom:9px;letter-spacing:.2px}
.footer-col a{color:var(--orange);text-decoration:none}
.read-more{display:inline-block;margin-top:5px;background:var(--orange);color:#fff;font-size:6.5px;line-height:13px;padding:0 4px;border-radius:1px}
.social{display:flex;gap:17px;margin-top:4px}
.social i{width:9px;height:9px;border-radius:50%;background:#eee;display:block}
.footer-bottom{left:0;top:1178px;width:690px;height:22px;background:var(--footer-low);font-size:6.5px;color:#bbb}
.footer-bottom span{position:absolute;top:6px}
</style>
</head>
<body>

<header class="site-header abs">
  <div class="brand abs"><i class="brand-mark"></i>Bright Nook</div>
  <div class="phone abs">
    <svg width="8" height="8" viewBox="0 0 24 24"><path fill="#333" d="M6.6 10.8a15 15 0 0 0 6.6 6.6l2.2-2.2c.3-.3.7-.4 1-.2 1.1.4 2.3.6 3.6.6.6 0 1 .4 1 1V20c0 .6-.4 1-1 1A17 17 0 0 1 3 4c0-.6.4-1 1-1h3.5c.6 0 1 .4 1 1 0 1.3.2 2.5.6 3.6.1.3 0 .7-.2 1z"/></svg>
    (505) 555-0182
  </div>
  <nav class="main-nav abs">
    <span class="active" style="left:274px">Home</span>
    <span style="left:318px">Our Services</span>
    <span style="left:386px">Our Employees</span>
    <span style="left:464px">Special Offers</span>
    <span style="left:537px">About Us</span>
    <span style="left:592px">Contact Us</span>
  </nav>
</header>

<section class="hero abs" role="img" aria-label="Photo of a housekeeper arranging cushions on a white sofa in a bright living room">
  <div class="hero-panel abs">
    <h1>Tell Annoying Enough To <b>CLEANING</b></h1>
    <p>Lorem ipsum dolor sit amet, consectetuer adipiscing elit, sed diam nonummy nibh euismod tincidunt ut laoreet dolore magna aliquam tation ullamcorper suscipit lobortis nisl ut aliquip ex ea commodo consequat.</p>
  </div>
</section>

<section class="welcome abs">
  <h2>Welcome to the <b>Bright Nook</b></h2>
  <p>Sed ut perspiciatis unde omnis iste natus error sit voluptatem accusantium doloremque laudantium, totam rem aperiam, eaque ipsa quae ab illo inventore veritatis et quasi architecto beatae vitae dicta sunt explicabo.</p>
</section>

<article class="service abs" style="left:58px">
  <div class="thumb" role="img" aria-label="Photo of a maid mopping a floor"></div>
  <div><h3>Maid Services</h3><p>Sed ut perspiciatis unde omnis iste natus error sit totam rem aperiam,</p></div>
</article>
<article class="service abs" style="left:258px">
  <div class="thumb" role="img" aria-label="Photo of a cleaner with a supply cart in a kitchen"></div>
  <div><h3>Kitchen Cleaning</h3><p>Sed ut perspiciatis unde omnis iste natus error sit totam rem aperiam,</p></div>
</article>
<article class="service abs" style="left:463px">
  <div class="thumb" role="img" aria-label="Photo of a maid making a bed"></div>
  <div><h3>Room Cleaning</h3><p>Sed ut perspiciatis unde omnis iste natus error sit totam rem aperiam,</p></div>
</article>

<div class="section-bar abs">
  <h3>Video's</h3>
  <svg width="14" height="8" viewBox="0 0 14 8"><path d="M4 1 1 4l3 3M10 1l3 3-3 3" fill="none" stroke="#444" stroke-width="1.2"/></svg>
</div>

<div class="video abs" role="img" aria-label="Video still of a cleaner wiping a kitchen counter">
  <div class="player-bar">
    <svg class="abs" style="left:17px;top:10px" width="10" height="12" viewBox="0 0 10 12"><path d="M0 0 10 6 0 12z" fill="#fff"/></svg>
    <div class="player-time">00:54:21 <span>/ 01:42:30</span></div>
    <svg class="abs" style="left:268px;top:11px" width="7" height="10" viewBox="0 0 7 10"><path d="M3 0h4v2H4v6.5A1.8 1.8 0 1 1 3 7z" fill="#fff"/></svg>
    <div class="abs" style="left:283px;top:15px;width:35px;height:2px;background:#c4282a"></div>
    <div class="abs" style="left:328px;top:0;width:1px;height:33px;background:#333"></div>
    <svg class="abs" style="left:340px;top:11px" width="10" height="10" viewBox="0 0 10 10"><path d="M0 0h4L0 4zM10 0v4L6 0zM0 10V6l4 4zM10 10H6l4-4zM3 3l4 4M7 3 3 7" fill="#fff" stroke="#fff" stroke-width="1"/></svg>
  </div>
</div>

<div class="video-copy abs">
  <p>Lorem ipsum dolor sit amet, consectetur adipisicing elit, sed do eiusmod tempor incididunt ut labore et dolore magna aliqua. Ut enim ad minim veniam,</p>
  <ul>
    <li>Sed ut perspiciatis unde omnis iste natus error</li>
    <li>Sit voluptatem accusantium doloremque laudantium</li>
    <li>Totam rem aperiam, eaque ipsa quae ab illo inventore</li>
    <li>Nemo enim ipsam voluptatem quia voluptas sit</li>
    <li>labore et dolore magnam aliquam quaerat</li>
    <li>vel illum qui dolorem eum fugiat quo voluptas nulla</li>
  </ul>
</div>
<div class="watch-btn abs">Watch Now</div>

<article class="sector abs" style="left:56px">
  <div class="photo" role="img" aria-label="Photo of a housekeeper tidying a sofa" style="background:linear-gradient(110deg,#d8c7a8,#f2eee8 50%,#e6e0d6)"></div>
  <h4>RESIDENTIAL</h4>
  <p>Lorem ipsum dolor sit amet, consectetur tellus vulputate fringilla.</p>
</article>
<article class="sector abs" style="left:254px">
  <div class="photo" role="img" aria-label="Photo of a janitor cleaning an airport terminal floor" style="background:linear-gradient(180deg,#7fb4cf,#3f6f86 55%,#1f3b45)"></div>
  <h4>COMMERCIAL</h4>
  <p>Lorem ipsum dolor sit amet, consectetur tellus vulputate fringilla.</p>
</article>
<article class="sector abs" style="left:453px">
  <div class="photo" role="img" aria-label="Photo of confetti and an empty bottle on a wooden floor after a party" style="background:linear-gradient(135deg,#e9c9a0,#d8ad7c 60%,#c99866)"></div>
  <h4>SPECIAL EVENTS</h4>
  <p>Lorem ipsum dolor sit amet, consectetur tellus vulputate fringilla.</p>
</article>

<div class="avatar abs" role="img" aria-label="Portrait of the client giving the testimonial"></div>
<div class="client-name abs">SAM CARTER, HARBOR STUDIO</div>
<div class="dots abs"><i class="on"></i><i></i><i></i><i></i><i></i></div>
<h2 class="testimonial-title abs">What <span>Client Say</span></h2>
<div class="quote abs" style="left:162px;top:928px">&ldquo;</div>
<p class="testimonial-text abs">Nam libero tempore, cum soluta nobis est eligendi optio cumque nihil impedit quo minus id quod maxime placeat facere possimus, omnis est, omnis dolor repellendus. Temporibus autem quibusdam et aut officiis debitis aut rerum necessitatibus saepe eveniet ut et voluptates repudiandae sint et molestiae non recusandae.</p>
<div class="quote abs" style="left:343px;top:976px">&rdquo;</div>

<footer class="site-footer abs"></footer>
<div class="footer-col abs" style="left:58px;width:160px">
  <h5>ABOUT US</h5>
  Plusieurs variations de Lorem Ipsum peuvent être trouvées ici ou là, mais la majeure partie d'entre elles a été altérée par l'addition d'humour ou de mots aléatoires qui.<br>
  <span class="read-more">Read More</span>
</div>
<div class="footer-col abs" style="left:258px">
  <h5>SITE MAP</h5>
  12 Harlow Row<br>Kelmsby<br>KB4 2PL<br>Phone:+44(0)1632 960417
</div>
<div class="footer-col abs" style="left:405px">
  <h5>NORTH AMERICA</h5>
  4180 Linden Park Dr<br>Suite 300<br>Maplewood, TX 77990<br>Phone:(713) 555 0146<br>Email: <a>Abcdef@example.com</a>
</div>
<div class="footer-col abs" style="left:549px">
  <h5>FOLLOW US</h5>
  <div class="social" aria-label="Social profiles"><i></i><i></i><i></i><i></i></div>
</div>
<div class="footer-bottom abs">
  <span style="left:58px">Home</span>
  <span style="left:89px">News</span>
  <span style="left:118px">About</span>
  <span style="left:149px">Soluions</span>
  <span style="left:189px">Contac Us</span>
  <span style="right:57px">© Copyrights 2013 All rights Reserved</span>
</div>

</body>
</html>
```